Business Card for a Jewellery Brand

Business card for an upscale jewellery brand. Attached is the brand logo and icon and color board. I am looking for two card versions: one for the founder and one is generic. The card should be elegant and convey upscale and premium feel. I am open to both square and rectangle card shapes.

Industry/Entity Type

Jewelry

Contact Information for Business Card

Two cards: (1) Sunela Parvaniya (Founder) (2) General
(1) Sunela Parvaniya card should have Name: Sunela Parvaniya, Title: Founder Email id: sunela@quiremo.com.au. Phone no: +61452913307
(2) Generic card should have Email id: info@quiremo.com.au. Phone no: +61436207518

Requirements
Must have
• Workmark
• ICON
• Phone no
• Email ID
• ABN: 58219740312 (Note: ABN is Business number in Australia)
• Website: www.quiremo.com.au
• Instagram: quiremo_jewellery
• Facebook: @quiremojewellery
Nice to have
• Tagline

```html
<!DOCTYPE html>
<html lang="en">
<head>
<meta charset="utf-8">
<title>Quiremo – Business Cards</title>
<link rel="stylesheet" href="https://fonts.googleapis.com/css2?family=Montserrat:wght@500&family=Raleway:wght@400;500&display=swap">
<style>
  :root {
    --page: #ffffff;
    --gold: #b8976a;
    --grey: #a3a4a8;
    --rule: #b9ab97;
    --marble-light: #f7f8f9;
    --marble-mid: #eceef0;
    --marble-shade: #e3e6e9;
  }
  * { margin: 0; padding: 0; box-sizing: border-box; }
  html, body {
    width: 1200px; height: 738px; overflow: hidden;
    background: var(--page);
  }
  .canvas { position: relative; width: 1200px; height: 738px; }

  .card {
    position: absolute; top: 138px;
    width: 466px; height: 462px;
  }
  .card--front { left: 92px; }
  .card--back { left: 643px; }

  .card__marble {
    position: absolute; inset: 0;
    background:
      linear-gradient(135deg, var(--marble-light) 0%, var(--marble-mid) 45%, var(--marble-light) 70%, var(--marble-shade) 100%);
  }

  .wordmark {
    position: absolute; left: 0; right: 0; top: 196px;
    text-align: center;
    font-family: "Raleway", sans-serif; font-weight: 500;
    font-size: 46px; letter-spacing: 0.3em; text-indent: 0.3em;
    color: var(--gold);
  }

  .social { position: absolute; left: 122px; display: flex; align-items: center; }
  .social--instagram { top: 358px; }
  .social--facebook { top: 404px; }
  .social__mark {
    width: 32px; height: 32px; border-radius: 4px;
    background: var(--gold); margin-right: 12px;
  }
  .social__handle {
    font-family: "Raleway", sans-serif; font-size: 24px;
    color: var(--gold);
  }

  .person { position: absolute; left: 52px; top: 76px; }
  .person__name {
    font-family: "Montserrat", sans-serif; font-weight: 500;
    font-size: 24px; color: var(--gold); line-height: 1.2;
  }
  .person__title {
    font-family: "Raleway", sans-serif; font-size: 20px;
    color: var(--grey); margin-top: 1px;
  }

  .divider {
    position: absolute; left: 146px; top: 270px;
    width: 172px; height: 1px; background: var(--rule);
  }

  .contact {
    position: absolute; left: 0; width: 464px; top: 290px;
    text-align: center; list-style: none;
    font-family: "Raleway", sans-serif; font-size: 20px;
    line-height: 29.6px; color: var(--grey);
  }
</style>
</head>
<body>
<main class="canvas">

  <section class="card card--front" aria-label="Card front">
    <div class="card__marble" role="img" aria-label="White marble texture with soft grey veining"></div>
    <div class="wordmark">QUIREMO</div>
    <div class="social social--instagram">
      <span class="social__mark" aria-hidden="true"></span>
      <span class="social__handle">quiremo_jewellery</span>
    </div>
    <div class="social social--facebook">
      <span class="social__mark" aria-hidden="true"></span>
      <span class="social__handle">@quiremojewellery</span>
    </div>
  </section>

  <section class="card card--back" aria-label="Card back">
    <div class="card__marble" role="img" aria-label="White marble texture with soft grey veining"></div>
    <div class="person">
      <p class="person__name">Sunela Parvaniya</p>
      <p class="person__title">Founder</p>
    </div>
    <div class="divider"></div>
    <ul class="contact">
      <li>+61452913307</li>
      <li>sunela@quiremo.com.au</li>
      <li>www.quiremo.com.au</li>
      <li>ABN: 58219740312</li>
    </ul>
  </section>

</main>
</body>
</html>
```